4747 5858

Web(re)design of an existing directory search site www.le5858.be (in Dutch www.de4747.be and in English www.3838.be).

This site is a directory site, i.e. a "white pages" site whereby people can search the phone & details of another person based on a combination of name + city (for instance smith in Brussels); one can also search a company also based on a combination of name + city (for instance Vornak in Brussels); last but not least one can also search the name of the subscriber behind a specific telephone number (also called reverse search).

This site is quite outdated and needs a redesign, see instructions.

We need the output in XD format.

```html
<!DOCTYPE html>
<html lang="en">
<head>
<meta charset="utf-8">
<title>58-58 — Information Fifty-Eight</title>
<link href="https://fonts.googleapis.com/css2?family=Roboto:wght@400;500;700&family=Russo+One&display=swap" rel="stylesheet">
<style>
:root{
  --red:#e21d24;
  --red-dark:#b5121a;
  --ink:#1d1d1f;
  --text:#5b5b5f;
  --page:#ffffff;
  --tint:#f6f7f9;
  --card:#f2f2f2;
  --card-line:#dcdcdc;
  --frame:#d9d9db;
  --footer:#1b2030;
  --footer-text:#e9eaee;
}
*{box-sizing:border-box;margin:0;padding:0}
html,body{width:1200px;height:2883px;overflow:hidden}
body{position:relative;background:var(--page);font-family:'Roboto',sans-serif;color:var(--ink)}
.abs{position:absolute}
.heading{font-family:'Russo One',sans-serif;font-weight:400;color:var(--ink);text-align:center}
.hero-bg{left:0;top:0;width:1200px;height:720px;background:var(--tint)}
.brand{left:112px;top:36px;display:flex;align-items:center;gap:10px;font-weight:700;font-size:30px;color:var(--red)}
.brand .dot{width:14px;height:14px;border-radius:50%;background:var(--red)}
.nav{top:46px;left:456px;display:flex;gap:31px;font-size:16px;font-weight:500}
.nav .lang{display:flex;align-items:center;gap:6px}
.nav .lang i{width:14px;height:14px;border-radius:50%;background:#c9cbd3;display:inline-block}
.login{left:964px;top:37px;width:123px;height:42px;border:2px solid var(--red);border-radius:21px;color:var(--red);font-size:16px;font-weight:500;display:flex;align-items:center;justify-content:center;gap:8px}
.hero-title{left:0;width:1200px;top:130px;font-size:35px}
.tabs{left:282px;top:194px;display:flex;gap:15px}
.tab{width:148px;height:44px;border:2px solid var(--ink);border-radius:22px;font-size:17px;font-weight:500;display:flex;align-items:center;justify-content:center;position:relative}
.tab.active{background:var(--red);border-color:var(--red);color:#fff}
.tab.active::after{content:"";position:absolute;bottom:-10px;left:66px;border:8px solid transparent;border-top-color:var(--red);border-bottom:0}
.laptop{left:291px;top:293px;width:629px;height:425px;border:3px solid #bdbdc0;border-radius:22px;background:var(--frame)}
.laptop .cam{position:absolute;left:310px;top:8px;width:12px;height:12px;border-radius:50%;background:#2a2a2a}
.screen{left:320px;top:320px;width:571px;height:338px;background:#f8f8f9;border:2px solid #bdbdc0;border-radius:14px}
.form label{position:absolute;left:365px;font-size:15px}
.form .field{position:absolute;left:365px;width:481px;height:43px;background:#fff;border:1px solid #e2e2e4;box-shadow:0 2px 6px rgba(0,0,0,.08);font-size:12px;color:#8b8b90;padding:14px 20px}
.search-btn{left:543px;top:591px;width:126px;height:42px;border-radius:21px;background:var(--red);color:#fff;font-size:17px;font-weight:500;display:flex;align-items:center;justify-content:center}
.art{border-radius:18px}
.person{left:132px;top:560px;width:150px;height:333px;background:linear-gradient(160deg,#e3403f 0%,#3c5a63 55%)}
.plant{left:930px;top:610px;width:140px;height:272px;background:linear-gradient(180deg,#2e4d53 0%,#aab3b5 60%,var(--red) 100%)}
.boxes{left:714px;top:764px;width:150px;height:116px;background:#e3e3e5;border-radius:6px}
.wallframe{background:#e9e9eb}
.floor{left:135px;top:880px;width:900px;height:2px;background:#cfcfd2}
.find-title{left:0;width:1200px;top:965px;font-size:35px}
.card{width:204px;height:169px;background:var(--card);border:2px solid var(--card-line);display:flex;flex-direction:column;align-items:center;padding-top:28px;gap:14px;font-size:19px;font-weight:500}
.card svg{width:74px;height:74px}
.explore-bg{left:0;top:1501px;width:1200px;height:397px;background:var(--tint)}
.explore-title{left:110px;top:1563px;font-size:34px;text-align:left}
.explore-copy{left:112px;top:1622px;width:410px;font-size:14.5px;line-height:26px;color:var(--text);text-align:justify}
.explore-copy p+p{margin-top:10px}
.pill{left:112px;top:1786px;width:165px;height:45px;border-radius:23px;background:var(--red);color:#fff;font-size:15px;font-weight:500;display:flex;align-items:center;justify-content:center}
.explore-art{left:600px;top:1580px;width:550px;height:316px;border-radius:160px 120px 0 0;background:linear-gradient(90deg,var(--red) 0%,#d7d7da 35%,#c9cbcf 65%,var(--red) 100%)}
.explore-line{left:595px;top:1896px;width:583px;height:2px;background:var(--ink)}
.use-title{left:0;width:1255px;top:1982px;font-size:35px}
.use{width:480px;height:130px}
.use .badge{position:absolute;left:0;top:6px;width:84px;height:84px;border-radius:50%;background:radial-gradient(circle at 40% 35%,var(--red),var(--red-dark));display:flex;align-items:center;justify-content:center}
.use .badge svg{width:42px;height:42px}
.use h3{position:absolute;left:107px;top:0;font-size:18px;font-weight:500}
.use p{position:absolute;left:107px;top:32px;width:370px;font-size:15px;line-height:24px;color:var(--text)}
.use a{position:absolute;left:107px;top:91px;font-size:15px;font-weight:500;color:var(--red);text-decoration:none;display:flex;align-items:center;gap:7px}
.use a i{width:13px;height:13px;border-radius:50%;background:var(--red);position:relative}
.use a i::after{content:"";position:absolute;left:4px;top:3px;border:3.5px solid transparent;border-left:5px solid #fff;border-right:0}
.footer{left:0;top:2568px;width:1200px;height:315px;background:var(--footer);color:var(--footer-text)}
.footer .brand{left:128px;top:84px;font-size:34px}
.socials{position:absolute;left:123px;top:182px;display:flex;gap:6px}
.socials span{width:26px;height:26px;border:1.5px solid #fff;border-radius:50%}
.fcol{position:absolute;top:66px}
.fcol h4{font-size:13.5px;font-weight:700;margin-bottom:16px;letter-spacing:.2px}
.fcol li{list-style:none;font-size:12px;line-height:26.5px}
.fcol p{font-size:12px;line-height:18px;width:300px}
.email{position:absolute;left:703px;top:155px;width:265px;height:47px;background:#fff;border:1px solid #ccc;color:#666;font-size:12px;padding:17px 19px}
.subscribe{position:absolute;left:976px;top:155px;width:111px;height:47px;background:var(--red);color:#fff;font-size:15px;font-weight:700;display:flex;align-items:center;justify-content:center}
.copyright{position:absolute;left:0;width:1200px;top:284px;text-align:center;font-size:11px}
</style>
</head>
<body>

<div class="abs hero-bg"></div>

<header>
  <div class="abs brand"><span class="dot"></span>58-58</div>
  <nav class="abs nav">
    <span>Popular Searches</span><span>Useful Numbers</span><span>Documents</span>
    <span class="lang"><i></i>Eng
      <svg width="10" height="6" viewBox="0 0 10 6"><path d="M0 0h10L5 6z" fill="#1d1d1f"/></svg></span>
  </nav>
  <div class="abs login">
    <svg width="11" height="13" viewBox="0 0 11 13"><rect x="0" y="5" width="11" height="8" rx="1" fill="#e21d24"/><path d="M2.5 5V3.5a3 3 0 0 1 6 0V5" stroke="#e21d24" stroke-width="1.8" fill="none"/></svg>
    Login
  </div>
</header>

<h1 class="abs heading hero-title">INFORMATION FIFTY-EIGHT - USEFUL FIFTY-EIGHT</h1>

<div class="abs tabs">
  <div class="tab active">Individuals</div>
  <div class="tab">Companies</div>
  <div class="tab">Inversed annual</div>
  <div class="tab">International</div>
</div>

<div class="abs wallframe" style="left:138px;top:298px;width:104px;height:102px" role="img" aria-label="Framed picture on the wall"></div>
<div class="abs wallframe" style="left:946px;top:294px;width:115px;height:160px" role="img" aria-label="Framed picture on the wall"></div>
<div class="abs wallframe" style="left:956px;top:490px;width:101px;height:100px" role="img" aria-label="Framed picture on the wall"></div>

<div class="abs floor"></div>
<div class="abs laptop"><span class="cam"></span></div>
<div class="abs screen"></div>
<form class="form">
  <label style="top:333px">Surname:</label>
  <div class="field" style="top:356px">Enter Surname</div>
  <label style="top:416px">First name:</label>
  <div class="field" style="top:439px">Enter First name</div>
  <label style="top:499px">Locality:</label>
  <div class="field" style="top:522px">Enter Locality</div>
  <div class="abs search-btn">58-58</div>
</form>

<div class="abs art person" role="img" aria-label="Illustration of a man on a bean bag chair using a laptop and phone"></div>
<div class="abs boxes" role="img" aria-label="Illustration of stacked storage boxes"></div>
<div class="abs art plant" role="img" aria-label="Illustration of a potted plant"></div>

<h2 class="abs heading find-title">WHAT CAN I FIND ON 58-58?</h2>

<div class="abs card" style="left:154px;top:1041px">
  <svg viewBox="0 0 64 64" aria-hidden="true"><path d="M8 40c0-14 10-24 24-24s24 10 24 24v6a4 4 0 0 1-4 4H12a4 4 0 0 1-4-4z" fill="#e21d24"/><path d="M22 26l4 10M32 24v12M42 26l-4 10" stroke="#fff" stroke-width="3" stroke-linecap="round"/></svg>
  Bakeries</div>
<div class="abs card" style="left:383px;top:1041px">
  <svg viewBox="0 0 64 64" aria-hidden="true"><circle cx="32" cy="20" r="12" fill="#e21d24"/><path d="M10 60c0-13 10-22 22-22s22 9 22 22z" fill="#e21d24"/><path d="M32 44v10M27 49h10" stroke="#fff" stroke-width="3.5"/></svg>
  Nurses</div>
<div class="abs card" style="left:612px;top:1041px">
  <svg viewBox="0 0 64 64" aria-hidden="true"><circle cx="33" cy="33" r="18" fill="none" stroke="#e21d24" stroke-width="5"/><circle cx="33" cy="33" r="9" fill="#e21d24"/><path d="M6 8v14a4 4 0 0 0 4 4v30M10 8v14M14 8v14a4 4 0 0 1-4 4" stroke="#e21d24" stroke-width="3" fill="none"/><path d="M58 8c-5 4-5 14-2 18v30" stroke="#e21d24" stroke-width="4" fill="none"/></svg>
  Restaurants</div>
<div class="abs card" style="left:841px;top:1041px">
  <svg viewBox="0 0 64 64" aria-hidden="true"><circle cx="32" cy="18" r="12" fill="#e21d24"/><path d="M8 60c0-13 10-24 24-24s24 11 24 24z" fill="#e21d24"/><path d="M22 38v10a5 5 0 0 0 10 0M42 38v12" stroke="#fff" stroke-width="2.5" fill="none"/><circle cx="42" cy="52" r="3" fill="#fff"/></svg>
  Doctors</div>
<div class="abs card" style="left:154px;top:1241px">
  <svg viewBox="0 0 64 64" aria-hidden="true"><rect x="4" y="18" width="12" height="40" rx="2" fill="#e21d24"/><path d="M16 24h5M16 30h5M16 36h5M16 42h5M16 48h5" stroke="#e21d24" stroke-width="2.5"/><path d="M34 6l14 38M58 6L44 44" stroke="#e21d24" stroke-width="4"/><circle cx="38" cy="52" r="6" fill="none" stroke="#e21d24" stroke-width="4"/><circle cx="54" cy="52" r="6" fill="none" stroke="#e21d24" stroke-width="4"/></svg>
  Hairdressers</div>
<div class="abs card" style="left:383px;top:1241px">
  <svg viewBox="0 0 64 64" aria-hidden="true"><path d="M4 58V14L32 4l28 10v44h-8V22H12v36z" fill="#e21d24"/><path d="M16 28h32M16 33h32" stroke="#e21d24" stroke-width="2.5"/><path d="M18 40l4-6h20l4 6v12h-28z" fill="#e21d24"/><circle cx="23" cy="46" r="2.5" fill="#fff"/><circle cx="41" cy="46" r="2.5" fill="#fff"/></svg>
  Garages</div>
<div class="abs card" style="left:612px;top:1241px">
  <svg viewBox="0 0 64 64" aria-hidden="true"><rect x="14" y="10" width="10" height="16" fill="#e21d24"/><rect x="28" y="14" width="8" height="12" fill="#e21d24"/><path d="M40 26l10-16 6 3-8 13" fill="#e21d24"/><path d="M4 26h56v6H4z" fill="#e21d24"/><path d="M8 34h48l-5 24H13z" fill="#e21d24"/><path d="M22 40v12M32 40v12M42 40v12" stroke="#fff" stroke-width="3"/></svg>
  Supermarkets</div>
<div class="abs card" style="left:841px;top:1241px">
  <svg viewBox="0 0 64 64" aria-hidden="true"><path d="M20 8c6 0 8 3 12 3s6-3 12-3c8 0 12 7 11 16-1 8-4 12-5 22-1 8-3 12-6 12-4 0-4-14-12-14s-8 14-12 14c-3 0-5-4-6-12-1-10-4-14-5-22C8 15 12 8 20 8z" fill="#e21d24"/></svg>
  Dentists</div>

<div class="abs explore-bg"></div>
<h2 class="abs heading explore-title">EXPLORE 58-58</h2>
<div class="abs explore-copy">
  <p>Lorem ipsum dolor sit amet, consectetur adipiscing elit, sed do eiusmod tempor incididunt ut labore et dolore magna aliqua. Ut nisi ut aliquip ex ea commodo consequat.</p>
  <p>Duis aute irure dolor in reprehenderit in voluptate velit esse cillum dolore eu fugiat nulla pariatur.</p>
</div>
<div class="abs pill">EXPLORE NOW</div>
<div class="abs explore-art" role="img" aria-label="Illustration of a woman reading a tablet on a red chair by a window"></div>
<div class="abs explore-line"></div>

<h2 class="abs heading use-title">HOW CAN I USE 58-58?</h2>

<div class="abs use" style="left:124px;top:2062px">
  <div class="badge"><svg viewBox="0 0 24 24" aria-hidden="true"><circle cx="12" cy="7.5" r="4" fill="none" stroke="#fff" stroke-width="1.4"/><path d="M4 22c0-5 3.5-8.5 8-8.5s8 3.5 8 8.5M12 13.5v8.5" fill="none" stroke="#fff" stroke-width="1.4"/></svg></div>
  <h3>Find a Person</h3>
  <p>Lorem ipsum dolor amet, consectetur adipiscing elit, sed do eiusmod tempor magna aliqua.</p>
  <a href="#">LEARN MORE <i></i></a>
</div>
<div class="abs use" style="left:621px;top:2062px">
  <div class="badge"><svg viewBox="0 0 24 24" aria-hidden="true"><path d="M6.6 10.8a15 15 0 0 0 6.6 6.6l2.2-2.2a1 1 0 0 1 1-.25 11.4 11.4 0 0 0 3.6.57 1 1 0 0 1 1 1V20a1 1 0 0 1-1 1A17 17 0 0 1 3 4a1 1 0 0 1 1-1h3.5a1 1 0 0 1 1 1c0 1.25.2 2.45.57 3.57a1 1 0 0 1-.25 1z" fill="none" stroke="#fff" stroke-width="1.4"/></svg></div>
  <h3>Look Up a Phone Number</h3>
  <p>Lorem ipsum dolor amet, consectetur adipiscing elit, sed do eiusmod tempor magna aliqua.</p>
  <a href="#">LEARN MORE <i></i></a>
</div>
<div class="abs use" style="left:124px;top:2206px">
  <div class="badge"><svg viewBox="0 0 24 24" aria-hidden="true"><path d="M12 22s7-7 7-12a7 7 0 0 0-14 0c0 5 7 12 7 12z" fill="none" stroke="#fff" stroke-width="1.4"/><circle cx="12" cy="10" r="2.8" fill="none" stroke="#fff" stroke-width="1.4"/></svg></div>
  <h3>Look Up an Address</h3>
  <p>Lorem ipsum dolor amet, consectetur adipiscing elit, sed do eiusmod tempor magna aliqua.</p>
  <a href="#">LEARN MORE <i></i></a>
</div>
<div class="abs use" style="left:621px;top:2206px">
  <div class="badge"><svg viewBox="0 0 24 24" aria-hidden="true"><rect x="4" y="3" width="13" height="18" rx="1.5" fill="none" stroke="#fff" stroke-width="1.4"/><path d="M7 9l1.5 1.5L11 8M7 14l1.5 1.5L11 13M13 9h2M13 14h2" fill="none" stroke="#fff" stroke-width="1.4"/><circle cx="17" cy="17" r="3" fill="#b5121a" stroke="#fff" stroke-width="1.4"/><path d="M19 19l2.5 2.5" stroke="#fff" stroke-width="1.4"/></svg></div>
  <h3>Get a Background Check</h3>
  <p>Lorem ipsum dolor amet, consectetur adipiscing elit, sed do eiusmod tempor magna aliqua.</p>
  <a href="#">LEARN MORE <i></i></a>
</div>
<div class="abs use" style="left:124px;top:2350px">
  <div class="badge"><svg viewBox="0 0 24 24" aria-hidden="true"><path d="M3 11l7-6 7 6v9H3z" fill="none" stroke="#fff" stroke-width="1.4"/><rect x="8" y="14" width="4" height="6" fill="none" stroke="#fff" stroke-width="1.4"/><circle cx="18" cy="16" r="2.5" fill="none" stroke="#fff" stroke-width="1.4"/><path d="M18 18.5V22M18 20.5h2" stroke="#fff" stroke-width="1.4"/></svg></div>
  <h3>Screen a Tenant</h3>
  <p>Lorem ipsum dolor amet, consectetur adipiscing elit, sed do eiusmod tempor magna aliqua.</p>
  <a href="#">LEARN MORE <i></i></a>
</div>
<div class="abs use" style="left:621px;top:2350px">
  <div class="badge"><svg viewBox="0 0 24 24" aria-hidden="true"><rect x="3" y="7" width="18" height="13" rx="1.5" fill="none" stroke="#fff" stroke-width="1.4"/><path d="M9 7V5h6v2M3 12h18M11 12v2h2v-2" fill="none" stroke="#fff" stroke-width="1.4"/></svg></div>
  <h3>Find a Business</h3>
  <p>Lorem ipsum dolor amet, consectetur adipiscing elit, sed do eiusmod tempor magna aliqua.</p>
  <a href="#">LEARN MORE <i></i></a>
</div>

<footer class="abs footer">
  <div class="abs brand"><span class="dot"></span>58-58</div>
  <div class="socials"><span></span><span></span><span></span><span></span></div>
  <div class="fcol" style="left:328px">
    <h4>COMPANY</h4>
    <ul><li>Home</li><li>About Us</li><li>Popular Searches</li><li>Useful Numbers</li><li>Documents</li></ul>
  </div>
  <div class="fcol" style="left:509px">
    <h4>INFORMATION</h4>
    <ul><li>Privacy and Security</li><li>Terms of Use</li><li>Site Map</li><li>Imprint</li></ul>
  </div>
  <div class="fcol" style="left:703px">
    <h4>SUBSCRIBE OUR NEWSLETTER</h4>
    <p>Subscribe to our mailing list to receives daily updates direct to your inbox!</p>
  </div>
  <div class="email">Email Address</div>
  <div class="subscribe">SUBSCRIBE</div>
  <div class="copyright">Copyrights © 5858 2022 | Allrights Reserved</div>
</footer>

</body>
</html>
```